Quillmarsh Property Solutions need a business card design

Hello guys. We would need a business card design asap please.
We are a start up property investment business based in London UK specialised in buying, selling, managing and letting properties and helping distressed property owners.
The name of our Business is Quillmarsh, the logo symbolises the four fundamental elements of the world (earth, air, fire and water) and so it stands for strength, stability, longevity.
We would like the business card to communicate professionalism and reliability. Many many thanks indeed for your work.

Details:

1.) Rosalind Updike
Property Investor
Mobile: +44(0)7700123456
Email: rosalind.quillmarsh@mailbox-example.com

2.) Dominic Updike
Property Investor
Mobile: +44(0)7700987654
Email: dominic.quillmarsh@mailbox-example.com

```html
<!DOCTYPE html>
<html lang="en">
<head>
<meta charset="utf-8">
<title>Quillmarsh Property Solutions – Business Card</title>
<link rel="stylesheet" href="https://fonts.googleapis.com/css2?family=Josefin+Sans:wght@700&family=Open+Sans:wght@400;600&display=swap">
<style>
  :root {
    --stage: #ecebe8;
    --card-white: #ffffff;
    --ink: #1b1b1b;
    --ink-soft: #555a5e;
    --accent-red: #c42a3c;
    --accent-blue: #2f56a8;
    --brand-green: #1e9e4a;
    --brand-green-light: #2cbb60;
    --brand-green-dark: #168a3d;
    --rule-green: #1f7a45;
  }
  * { box-sizing: border-box; margin: 0; padding: 0; }
  html, body {
    width: 1200px;
    height: 720px;
    overflow: hidden;
    background: var(--stage);
  }
  .canvas {
    width: 1200px;
    height: 720px;
    display: flex;
    align-items: center;
    justify-content: center;
    gap: 40px;
  }
  .card {
    position: relative;
    width: 540px;
    height: 309px;
    box-shadow: 0 6px 18px rgba(0,0,0,0.16);
    overflow: hidden;
  }

  /* Front */
  .card--front { background: var(--card-white); }
  .brand {
    position: absolute;
    left: 38px;
    top: 92px;
  }
  .brand__row {
    display: flex;
    align-items: center;
    gap: 10px;
  }
  .brand__square {
    width: 22px;
    height: 22px;
    background: var(--brand-green);
  }
  .brand__name {
    font-family: "Josefin Sans", sans-serif;
    font-weight: 700;
    font-size: 27px;
    letter-spacing: 1.5px;
    color: var(--ink);
    line-height: 1;
    padding-top: 4px;
  }
  .brand__tagline {
    font-family: "Josefin Sans", sans-serif;
    font-weight: 700;
    font-size: 9.5px;
    letter-spacing: 1px;
    color: var(--ink);
    margin-top: 5px;
    margin-left: 32px;
  }
  .person {
    position: absolute;
    left: 38px;
    top: 200px;
    font-family: "Open Sans", sans-serif;
  }
  .person__name {
    font-weight: 600;
    font-size: 17px;
    color: var(--accent-red);
    line-height: 1.15;
  }
  .person__role {
    font-size: 13px;
    color: var(--accent-blue);
  }
  .contact {
    position: absolute;
    left: 272px;
    top: 150px;
    height: 94px;
    padding-left: 14px;
    border-left: 2px solid var(--rule-green);
    font-family: "Open Sans", sans-serif;
    font-size: 10.5px;
    color: var(--ink-soft);
  }
  .contact__item {
    display: flex;
    align-items: center;
    gap: 6px;
    line-height: 1.9;
  }
  .contact__icon { width: 11px; height: 11px; flex: none; }

  /* Back */
  .card--back {
    background: radial-gradient(ellipse at 45% 40%, var(--brand-green-light) 0%, var(--brand-green) 55%, var(--brand-green-dark) 100%);
    display: flex;
    align-items: center;
    justify-content: center;
  }
  .back-brand {
    display: flex;
    align-items: center;
    gap: 14px;
  }
  .back-brand__square {
    width: 34px;
    height: 34px;
    background: var(--card-white);
  }
  .back-brand__name {
    font-family: "Josefin Sans", sans-serif;
    font-weight: 700;
    font-size: 40px;
    letter-spacing: 2px;
    color: var(--card-white);
    padding-top: 6px;
  }
</style>
</head>
<body>
<main class="canvas">
  <section class="card card--front">
    <div class="brand">
      <div class="brand__row">
        <span class="brand__square"></span>
        <span class="brand__name">QUILLMARSH</span>
      </div>
      <div class="brand__tagline">PROPERTY SOLUTIONS</div>
    </div>
    <div class="person">
      <p class="person__name">Dominic Updike</p>
      <p class="person__role">Property Investor</p>
    </div>
    <div class="contact">
      <p class="contact__item">
        <svg class="contact__icon" viewBox="0 0 12 12" aria-hidden="true">
          <rect x="3" y="0.5" width="6" height="11" rx="1.2" fill="var(--accent-blue)"/>
          <rect x="4" y="2" width="4" height="6" fill="#fff"/>
        </svg>
        <span>+44(0)7700987654</span>
      </p>
      <p class="contact__item">
        <svg class="contact__icon" viewBox="0 0 12 12" aria-hidden="true">
          <rect x="0.5" y="2.5" width="11" height="7.5" rx="1" fill="var(--accent-blue)"/>
          <path d="M1 3 L6 7 L11 3" stroke="#fff" stroke-width="1" fill="none"/>
        </svg>
        <span>dominic.quillmarsh@mailbox-example.com</span>
      </p>
    </div>
  </section>

  <section class="card card--back">
    <div class="back-brand">
      <span class="back-brand__square"></span>
      <span class="back-brand__name">QUILLMARSH</span>
    </div>
  </section>
</main>
</body>
</html>
```